NZ First of it's kind solutions directory and marketplace for busy Mums needs a business card design

We need a business card design for our new nationwide business in NZ (long term plans to go global). We provide solutions to the everyday challenges that busy Mums face by connecting them with quality communities and suppliers of carefully selected, relevant products and services. We sell direct via our online marketplace. The final design should communicate our values of inclusivity, quality and smart solutions. Colours should incorporate our logo colour palette of #477077 and #6ba8b2. Our website is at https://www.brightnestmums.example

Target Market(s)

busy Mums, Age 28 – 50, female, income over $100K, location main centres NZ primarily but NZ wide. Is likely juggling work or career with a young family. Probably had hobbies which have fallen by the wayside.
-Wants to succeed in her chosen career without compromising on family life
-to successfully juggle her career without feeling like she is compromising her children
- Is time poor, something always has to give and it’s generally her health (she’ll stay up late, get stressed)
- probably ex corporate or professional career. Has discretional income

Industry/Entity Type

Business

Contact Information for Business Card

Lena Forbisher, Founder, BrightNestMums.example (Strapline Tap; Gather; Sorted), 47 Kowhai Terrace, Ellerslie, Auckland 1051, New Zealand. Mob: 021 483 517 Ph: +64 (0)9 571 4860

Font styles to use
Other font styles liked:
• Raleway, and/or Architects Daughter

Colors
00a990
33b8a4
86cfc6
cfeae6

Requirements
Must have
• the above details, streamline. the logo and colours associated with those logos
Should not have
• foil or metallic colours

```html
<!DOCTYPE html>
<html lang="en">
<head>
<meta charset="utf-8">
<title>BrightNestMums – Business Card</title>
<link href="https://fonts.googleapis.com/css2?family=Raleway:wght@500;600;700;800&display=swap" rel="stylesheet">
<style>
  :root {
    --teal-dark: #477077;
    --teal-light: #6ba8b2;
    --card-top: #6aa7b0;
    --card-bottom: #4a7279;
    --white: #ffffff;
    --stage: #2a2a2a;
  }
  * { box-sizing: border-box; margin: 0; padding: 0; }
  html, body {
    width: 1189px; height: 1200px; overflow: hidden;
    background: var(--stage);
    font-family: "Raleway", Arial, sans-serif;
  }
  .canvas { position: relative; width: 1189px; height: 1200px; }
  .card {
    position: absolute; left: 171px; width: 856px; height: 488px;
    border-radius: 24px; overflow: hidden;
  }
  .card--front {
    top: 67px;
    background: linear-gradient(to bottom, var(--card-top), var(--card-bottom));
  }
  .card--back { top: 626px; background: var(--white); }

  .brand {
    position: absolute; left: 0; right: 0;
    display: flex; align-items: center; justify-content: center; gap: 18px;
    font-weight: 800; font-size: 60px; letter-spacing: -1px; line-height: 1;
  }
  .brand__dot { width: 40px; height: 40px; border-radius: 50%; }
  .card--front .brand { top: 216px; color: var(--white); }
  .card--front .brand__dot { background: var(--white); }
  .card--back .brand { top: 111px; color: var(--teal-dark); }
  .card--back .brand__dot { background: var(--teal-light); }

  .front-web {
    position: absolute; left: 0; right: 0; top: 350px; text-align: center;
    color: var(--white); font-size: 20px; font-weight: 500; letter-spacing: 2.5px;
  }
  .front-web strong { font-weight: 700; }

  .name-band {
    position: absolute; left: 0; right: 0; top: 252px; height: 59px;
    background: var(--teal-dark); color: var(--white); text-align: center;
  }
  .name-band__name { font-weight: 800; font-size: 25px; line-height: 1; padding-top: 8px; letter-spacing: -0.3px; }
  .name-band__role { font-weight: 500; font-size: 19px; line-height: 1.1; }

  .details {
    position: absolute; left: 0; right: 0; top: 315px; height: 147px; display: flex;
  }
  .details__address {
    width: 428px; background: var(--teal-dark); color: var(--white);
    text-align: right; padding: 34px 35px 0 0; font-size: 21px; font-weight: 500; line-height: 27px;
  }
  .details__contact {
    flex: 1; background: var(--teal-light); color: var(--white);
    padding: 33px 0 0 33px; font-size: 21px; font-weight: 500; line-height: 27px; list-style: none;
  }
  .details__contact li { display: flex; align-items: center; gap: 10px; }
  .details__contact svg { width: 16px; height: 16px; flex: none; }
</style>
</head>
<body>
<main class="canvas">
  <section class="card card--front" aria-label="Card front">
    <div class="brand"><span class="brand__dot"></span><span>BrightNestMums</span></div>
    <p class="front-web">www.<strong>brightnestmums</strong>.example</p>
  </section>

  <section class="card card--back" aria-label="Card back">
    <div class="brand"><span class="brand__dot"></span><span>BrightNestMums</span></div>
    <div class="name-band">
      <p class="name-band__name">Lena Forbisher</p>
      <p class="name-band__role">Founder</p>
    </div>
    <div class="details">
      <address class="details__address" style="font-style:normal">
        47 Kowhai Terrace<br>Ellerslie, Auckland 1051<br>New Zealand
      </address>
      <ul class="details__contact">
        <li>
          <svg viewBox="0 0 16 16" aria-hidden="true"><rect x="4" y="1.5" width="8" height="13" rx="1.5" fill="none" stroke="#fff" stroke-width="1.6"/><circle cx="8" cy="12" r="0.9" fill="#fff"/></svg>
          021 483 517
        </li>
        <li>
          <svg viewBox="0 0 16 16" aria-hidden="true"><path d="M2 6c0-2 3-3 6-3s6 1 6 3l-2.5 1L10 5.5H6L4.5 7z" fill="#fff"/><rect x="3.5" y="8" width="9" height="5" rx="1" fill="#fff"/></svg>
          +64 (0)9 571 4860
        </li>
        <li>
          <svg viewBox="0 0 16 16" aria-hidden="true"><g fill="none" stroke="#fff" stroke-width="1.2"><circle cx="8" cy="8" r="6.3"/><ellipse cx="8" cy="8" rx="2.8" ry="6.3"/><path d="M1.7 8h12.6M3 4.5h10M3 11.5h10"/></g></svg>
          www.brightnestmums.example
        </li>
      </ul>
    </div>
  </section>
</main>
</body>
</html>
```